business card

Business card for new business.
Red and black corporate colors.
Card can have an Indsutrial feel to it. Feel free to add Rust, Bolted steel, or graphics as you see fit. We provide highly specialized services to the below mentioned industries.
Keep information out of corners so that if I want I can choose rounded corners.
Information
- front. name - title - phone - email
- Rear
Refining - Rail - Infrastructure - Mining - Energy
Ridgeford - Halbrook - Port Carrowby - Ashcombe - Westmere

```html
<!DOCTYPE html>
<html lang="en">
<head>
<meta charset="utf-8">
<title>Girderline business card</title>
<link rel="stylesheet" href="https://fonts.googleapis.com/css2?family=Roboto+Condensed:wght@400;700&family=Roboto:wght@400;500&display=swap">
<style>
  :root {
    --backdrop: #262626;
    --steel-light: #f2f2f2;
    --steel-mid: #dcdcdc;
    --steel-dark: #bdbdbd;
    --brush-line: rgba(255, 255, 255, 0.35);
    --brush-shade: rgba(0, 0, 0, 0.04);
    --brand-red: #e50019;
    --ink-grey: #7a7a7a;
    --ink-dark: #4a4a4a;
    --white: #ffffff;
  }
  html, body {
    margin: 0;
    padding: 0;
    width: 1200px;
    height: 960px;
    overflow: hidden;
    background: var(--backdrop);
  }
  .canvas {
    position: relative;
    width: 1200px;
    height: 960px;
  }
  .card {
    position: absolute;
    width: 600px;
    height: 343px;
    box-sizing: border-box;
  }
  .card-front {
    left: 314px;
    top: 113px;
    background:
      repeating-linear-gradient(90deg, var(--brush-line) 0 1px, transparent 1px 4px, var(--brush-shade) 4px 5px, transparent 5px 9px),
      linear-gradient(90deg, var(--steel-dark) 0%, var(--steel-light) 22%, var(--steel-mid) 48%, var(--steel-light) 72%, var(--steel-dark) 100%);
  }
  .card-back {
    left: 311px;
    top: 472px;
    background: var(--brand-red);
  }
  .wordmark {
    position: absolute;
    left: 0;
    right: 0;
    text-align: center;
    font-family: "Roboto Condensed", sans-serif;
    font-weight: 700;
    letter-spacing: 1px;
    line-height: 1;
  }
  .card-front .wordmark {
    top: 102px;
    font-size: 58px;
    color: var(--ink-grey);
  }
  .card-back .wordmark {
    top: 124px;
    font-size: 62px;
    color: var(--white);
  }
  .holder {
    position: absolute;
    top: 264px;
    left: 0;
    right: 0;
    text-align: center;
    font-family: "Roboto Condensed", sans-serif;
    line-height: 1;
  }
  .holder-name {
    font-weight: 700;
    font-size: 22px;
    color: var(--brand-red);
  }
  .holder-title {
    font-weight: 400;
    font-size: 16px;
    color: var(--ink-grey);
  }
  .contact {
    position: absolute;
    top: 294px;
    left: 0;
    right: 0;
    text-align: center;
    font-family: "Roboto", sans-serif;
    font-size: 14.5px;
    color: var(--ink-dark);
    line-height: 1;
  }
  .contact-label {
    color: var(--brand-red);
  }
  .sectors {
    position: absolute;
    top: 257px;
    left: 0;
    right: 0;
    margin: 0;
    text-align: center;
    font-family: "Roboto", sans-serif;
    font-size: 14.5px;
    line-height: 18px;
    color: var(--white);
  }
</style>
</head>
<body>
<main class="canvas">
  <section class="card card-front" aria-label="Card front">
    <div class="wordmark">GIRDERLINE</div>
    <div class="holder">
      <span class="holder-name">DALE MERCER -</span>
      <span class="holder-title">CEO/FOUNDER</span>
    </div>
    <div class="contact">
      <span class="contact-label">P</span>. 604 555 0193
      <span class="contact-label">E</span> . info@girderline.com
      <span class="contact-label">W</span>. www.girderline.com
    </div>
  </section>

  <section class="card card-back" aria-label="Card back">
    <div class="wordmark">GIRDERLINE</div>
    <p class="sectors">
      Refining • Rail • Infrastructure • Mining<br>
      Energy • Ridgeford • Halbrook • Port Carrowby<br>
      Ashcombe • Westmere
    </p>
  </section>
</main>
</body>
</html>
```